Classy, Elegant, Simple Business Card Design

Looking to have a classy, simple, and elegant design. Want a top notch designed business card. I really like the look of the new torvane credit card. I also like the design I attached. I am trying to reach 21-29 year old females for booking us for there wedding or event. We offer Disc Jockey Service, Photo Booth Rentals, and Uplighting .

Target Market(s)

21-28 year old females

Contact Information for Business Card

Has to have logo, website, email, and phone number

Font styles to use
Other font styles liked:
• open to font choice, modern, clean
Designer to choose
33a6d7
0791cd
0555a3
ffffff

Requirements
Must have
• Has to have logo, website, email, and phone number
Nice to have
• I really like the design of the new torvane credit card. I also included my logo and some designs I like
Should not have
• clutter or too much info

```html
<!DOCTYPE html>
<html lang="en">
<head>
<meta charset="utf-8">
<title>Tidelight Event Group – Business Card</title>
<link rel="stylesheet" href="https://fonts.googleapis.com/css2?family=Questrial&family=Ubuntu:wght@500;700&family=Roboto:wght@400&display=swap">
<style>
  :root {
    --page-bg: #e9e7e4;
    --card-bg: #f4f5f6;
    --card-edge: #d9dcdf;
    --brand-light: #33a6d7;
    --brand-mid: #0791cd;
    --brand-deep: #0555a3;
    --ink: #2a2f36;
    --ink-soft: #3c4148;
    --wave-tone: #7c838b;
  }
  * { margin: 0; padding: 0; box-sizing: border-box; }
  html, body {
    width: 1200px;
    height: 1054px;
    overflow: hidden;
    background: var(--page-bg);
  }
  .business-card {
    position: absolute;
    left: 100px;
    top: 227px;
    width: 1000px;
    height: 600px;
    background: var(--card-bg);
    border: 1px solid var(--card-edge);
    border-radius: 4px;
    box-shadow: 0 12px 40px rgba(0, 0, 0, 0.12);
    overflow: hidden;
  }
  .brand {
    position: absolute;
    left: 180px;
    top: 128px;
    display: flex;
    align-items: center;
    gap: 22px;
  }
  .brand-dot {
    width: 58px;
    height: 58px;
    border-radius: 50%;
    background: var(--brand-mid);
  }
  .brand-divider {
    width: 2px;
    height: 100px;
    background: var(--wave-tone);
    opacity: 0.45;
  }
  .brand-name {
    font-family: "Questrial", "Century Gothic", sans-serif;
    font-size: 38px;
    letter-spacing: 1px;
    color: var(--brand-deep);
    line-height: 1;
  }
  .person {
    position: absolute;
    right: 520px;
    top: 356px;
    text-align: right;
  }
  .person-name {
    font-family: "Ubuntu", sans-serif;
    font-weight: 700;
    font-size: 43px;
    color: var(--brand-deep);
    line-height: 1.1;
  }
  .person-role {
    font-family: "Ubuntu", sans-serif;
    font-weight: 500;
    font-size: 23px;
    color: var(--ink-soft);
    margin-top: 6px;
  }
  .contact-list {
    position: absolute;
    left: 500px;
    top: 340px;
    list-style: none;
  }
  .contact-item {
    display: flex;
    align-items: center;
    gap: 20px;
    height: 39px;
    font-family: "Roboto", sans-serif;
    font-size: 25px;
    color: var(--ink);
  }
  .contact-icon { width: 24px; height: 24px; flex: none; }
  .sound-band {
    position: absolute;
    left: 0;
    bottom: 0;
    width: 100%;
    height: 78px;
    background: linear-gradient(to top, rgba(124,131,139,0.55), rgba(124,131,139,0.08));
  }
</style>
</head>
<body>
  <section class="business-card">
    <div class="brand">
      <span class="brand-dot"></span>
      <span class="brand-divider"></span>
      <span class="brand-name">TIDELIGHT EVENT GROUP</span>
    </div>

    <div class="person">
      <p class="person-name">Mara Ellison</p>
      <p class="person-role">Founder &amp; CEO</p>
    </div>

    <ul class="contact-list">
      <li class="contact-item">
        <svg class="contact-icon" viewBox="0 0 24 24" aria-hidden="true">
          <path fill="#3c4148" d="M3 9c0-3 4-5 9-5s9 2 9 5v2h-5V9c-1-1-3-1.5-4-1.5S9 8 8 9v2H3z"/>
          <rect x="6" y="12" width="12" height="8" rx="1.5" fill="#3c4148"/>
        </svg>
        <span>555 0142 0188</span>
      </li>
      <li class="contact-item">
        <svg class="contact-icon" viewBox="0 0 24 24" aria-hidden="true">
          <rect x="2" y="5" width="20" height="14" rx="1" fill="#3c4148"/>
          <path d="M3 6l9 7 9-7" fill="none" stroke="#f4f5f6" stroke-width="1.8"/>
        </svg>
        <span>mara@tidelight.com</span>
      </li>
      <li class="contact-item">
        <svg class="contact-icon" viewBox="0 0 24 24" aria-hidden="true">
          <circle cx="12" cy="12" r="9.5" fill="#3c4148"/>
          <path d="M2.5 12h19M12 2.5c3 3 3 16 0 19M12 2.5c-3 3-3 16 0 19" fill="none" stroke="#f4f5f6" stroke-width="1.3"/>
        </svg>
        <span>www.tidelight.com</span>
      </li>
    </ul>

    <div class="sound-band" role="img" aria-label="Decorative sound waveform strip along the bottom edge"></div>
  </section>
</body>
</html>
```